VELMA, an e-commerce website with a twist, providing consumer-to-consumer and business-to-consumer sa

I have only uploaded 10 wire-frame pages of the website. These pages have been chosen for the different lay-outs and should give an idea of what will be needed. There are many more that I won’t upload yet, I aim to choose a winner first then there will be a high possibility that the winner will get the chance to do the design work for these later.
The design I have in mind is to keep it clean and easy with no/minimal fancy fonts and hieroglyphics. The logo is white with an orange highlight on a solid background of black, please note that the logo is white on a black background and is not a black box with white lettering, trust that makes sense. I like the idea of the top part of the website being black all the way across. I don’t see the need for more than 3 colours in the actual base website (the pictures and adverts added by users will add other colours). Although orange is the highlight colour in the logo I am open to suggestions on this, so long as the highlight colour features throughout the site.

Website width is 1220px, all pages in the PDF are 1220px

Logo font is Rezlong

The company is going to be like tradu, but much more focused on raising money for charity and humanitarian relief.

Target Market(s)

the modern era of smartphones and the sharing community

Industry/Entity Type

Business

Number of Pages Required

5+ page

Font styles to use
Sans Serif
Other font styles liked:
• rezlong

Colors
faa54b
f78f20
ffffff
000000
fbfbfb
f5f5f5

Requirements
Nice to have
• Although orange is the highlight colour in the logo I am open to suggestions on this, so long as the highlight colour features throughout the site.

```html
<!DOCTYPE html>
<html lang="en">
<head>
<meta charset="utf-8">
<title>Velma – Home</title>
<link rel="stylesheet" href="https://fonts.googleapis.com/css2?family=Open+Sans:wght@400;600;700&family=Comfortaa:wght@400;700&family=Oswald:wght@400&display=swap">
<style>
:root{
  --orange:#f78f20;
  --orange-soft:#faa54b;
  --black:#000000;
  --ink:#222222;
  --white:#ffffff;
  --paper:#fbfbfb;
  --mist:#f2f2f2;
  --line:#cfcfcf;
  --footer:#1b1b1b;
}
*{box-sizing:border-box;margin:0;padding:0}
html,body{width:1200px;height:2514px;overflow:hidden;background:var(--white)}
body{font-family:"Open Sans",Arial,sans-serif;color:var(--ink)}
.canvas{position:relative;width:1200px;height:2514px;overflow:hidden;background:var(--white)}
.abs{position:absolute}

/* top bar */
.topbar{top:0;left:0;width:1200px;height:67px;background:var(--white)}
.topbar .links{position:absolute;top:20px;font-size:16px;font-weight:600;color:var(--black)}
.topbar .links span.sep{margin:0 12px;font-weight:400}
.topbar .left{left:30px}
.topbar .right{right:220px}
.search-box{position:absolute;left:999px;top:13px;width:171px;height:38px;border:1px solid var(--line);border-radius:3px;font-size:14px;color:#888;padding:9px 8px}

/* header */
.header{top:67px;left:0;width:1200px;height:94px;background:var(--orange)}
.header svg.shape{position:absolute;left:0;top:0}
.brand{position:absolute;left:30px;top:14px;font-family:"Comfortaa",sans-serif;font-weight:700;font-size:58px;color:var(--white);letter-spacing:-1px}
.hdr-item{position:absolute;top:30px;color:var(--white);font-size:21px;display:flex;align-items:center;gap:8px}
.hdr-item b{font-weight:600}
.hdr-item .ring{width:40px;height:40px;border-radius:50%;border:2px solid var(--white);display:flex;align-items:center;justify-content:center}
.acct{position:absolute;top:36px;font-size:16px;font-weight:600;color:var(--white);display:flex;gap:10px;align-items:center}
.acct .sep{font-weight:400;margin:0 6px}

/* hero */
.hero{top:161px;left:0;width:1200px;height:660px;background:linear-gradient(180deg,#ececec,#e4e4e4)}
.section-label{position:absolute;color:var(--orange);font-size:23px;font-weight:600;text-align:center;width:357px;left:30px}
.video{position:absolute;left:30px;width:357px;height:190px;border:2px solid #c8c8c8;background:var(--white);padding:3px}
.video .screen{width:100%;height:150px;display:flex;align-items:center;justify-content:center}
.video .controls{height:30px;display:flex;align-items:center;gap:8px;padding:0 8px}
.video .progress{flex:1;height:3px;background:#333}
.play{width:62px;height:62px;border-radius:50%;background:var(--white);display:flex;align-items:center;justify-content:center}

.finder{top:211px;left:407px;width:436px;height:553px;background:var(--orange)}
.finder .photo{position:absolute;left:17px;top:17px;width:401px;height:176px;background:radial-gradient(ellipse at 50% 55%,#2a3f6e 0%,#6b5a4d 35%,#d9d6d2 75%)}
.field{position:absolute;height:52px;border:2px solid var(--white);color:var(--white);font-size:17px;padding:13px 12px;display:flex;justify-content:space-between;align-items:center}
.field .q{width:18px;height:18px;border-radius:50%;background:var(--white);color:var(--orange);font-size:13px;font-weight:700;display:flex;align-items:center;justify-content:center}
.finder .lbl{position:absolute;left:14px;color:var(--white);font-size:17px;font-weight:600}
.btn-search{position:absolute;left:82px;top:479px;width:148px;height:52px;background:var(--white);color:var(--orange);font-size:19px;display:flex;align-items:center;justify-content:center}

.promo{position:absolute;left:863px;width:307px;height:118px}
.promo .thumb{position:absolute;left:0;top:0;width:129px;height:118px;border:2px solid #d5d5d5;background:var(--white);display:flex;align-items:center;justify-content:center}
.promo .thumb i{display:block;width:60px;height:86px;border-radius:8px;background:linear-gradient(135deg,#666,#111 60%,#888)}
.promo h3{position:absolute;left:149px;top:6px;font-size:17px;font-weight:600;color:var(--black);white-space:nowrap;line-height:24px}
.promo p{position:absolute;left:149px;top:38px;width:162px;font-size:14px;line-height:21px;color:var(--black)}
.promo a{position:absolute;left:149px;top:95px;font-size:14px;font-weight:600;color:var(--orange);text-decoration:none}
.rule{position:absolute;left:863px;width:307px;height:2px;background:#c9c9c9}

/* banner */
.banner{top:865px;left:30px;width:1140px;height:265px;overflow:hidden;background:radial-gradient(ellipse at 40% 35%,#6a6e74 0%,#2f3238 45%,#15171b 100%)}
.banner svg{position:absolute;left:0;top:0}
.banner .mark{position:absolute;right:38px;top:56px;font-family:"Comfortaa",sans-serif;font-weight:700;font-size:54px;line-height:70px;color:var(--white);white-space:nowrap}
.banner .tag{position:absolute;right:37px;top:160px;font-family:"Oswald",sans-serif;font-size:33px;line-height:44px;color:var(--white);letter-spacing:.3px;white-space:nowrap}

/* feedback */
.feedback{top:1183px;left:0;width:1200px;height:580px;background:var(--mist)}
.title-round{font-family:"Comfortaa",sans-serif;font-weight:700;color:var(--orange);white-space:nowrap}
.feedback h2{position:absolute;left:0;width:1200px;top:48px;text-align:center;font-size:40px}
.feedback .underline{position:absolute;left:530px;top:116px;width:140px;height:2px;background:var(--orange)}
.quote{position:absolute;top:198px;width:369px;height:215px}
.quote svg{position:absolute;left:0;top:-23px;overflow:visible}
.quote p{position:absolute;left:20px;top:50px;width:330px;font-size:15px;line-height:28px;text-align:justify;color:var(--black)}
.quote.featured p{color:var(--white)}
.quote .name{position:absolute;left:32px;top:208px;font-size:18px;font-weight:600;color:var(--orange)}
.feedback .cta{position:absolute;left:0;width:1200px;top:498px;text-align:center;font-size:20px;font-weight:600;color:var(--orange);text-decoration:underline}

/* charities */
.charities{top:1763px;left:0;width:1200px;height:550px;background:var(--white)}
.charities h2{position:absolute;left:27px;top:44px;font-size:38px;letter-spacing:-0.5px}
.charities .underline{position:absolute;left:27px;top:102px;width:146px;height:2px;background:var(--orange)}
.badge{position:absolute;width:158px;height:82px;border:2px solid #d5d5d5;border-radius:3px;display:flex;align-items:center;justify-content:center}
.badge i{display:block;width:84px;height:44px;border:2px solid #555;border-radius:6px}
.badge i.round{border-radius:50%}
.feature{position:absolute;left:630px;width:540px;height:201px}
.feature span{position:absolute;font-family:"Comfortaa",sans-serif;font-weight:700;font-size:35px;color:var(--white);white-space:nowrap}

/* footer */
.footer{top:2313px;left:0;width:1200px;height:201px;background:var(--footer)}
.footer .nav{position:absolute;left:30px;top:43px;font-size:15px;font-weight:600;color:var(--white)}
.footer .nav .sep{margin:0 8px;font-weight:400}
.social{position:absolute;right:30px;top:42px;display:flex;gap:9px}
.social i{display:block;width:18px;height:18px;border-radius:4px;background:var(--white)}
.footer hr{position:absolute;left:30px;top:103px;width:1140px;border:0;height:1px;background:#444}
.footer .copy{position:absolute;left:30px;top:138px;font-size:17px;color:var(--white)}
.footer .meta{position:absolute;right:30px;top:138px;font-size:17px;color:var(--white)}
.footer .meta .sep{margin:0 12px}
</style>
</head>
<body>
<div class="canvas">

  <div class="abs topbar">
    <div class="links left">Notifications<span class="sep">|</span>News<span class="sep">|</span>List Item</div>
    <div class="links right">Contact Us<span class="sep">|</span>Help<span class="sep">|</span>Terms &amp; Conditions</div>
    <div class="search-box">Search</div>
  </div>

  <header class="abs header">
    <svg class="shape" width="320" height="94"><polygon points="0,0 315,0 277,94 0,94" fill="#000"/></svg>
    <div class="brand">velma</div>
    <div class="hdr-item" style="left:347px">
      <span class="ring"><svg width="20" height="20" viewBox="0 0 20 20"><path d="M4 7h12l-1 11H5z" fill="#fff"/><path d="M7 7V5a3 3 0 0 1 6 0v2" stroke="#fff" stroke-width="2" fill="none"/></svg></span>
      <span><b>Cart:</b> 0items</span>
    </div>
    <div class="hdr-item" style="left:525px">
      <span class="ring"><svg width="20" height="20" viewBox="0 0 20 20"><path d="M10 17 3 10a4 4 0 0 1 7-5 4 4 0 0 1 7 5z" fill="#fff"/></svg></span>
      <span><b>Wishlist:</b> 0items</span>
    </div>
    <div class="acct" style="left:760px">
      <span>&#10140; Sign In</span><span class="sep">|</span>
      <span>&#9679; My Account</span><span class="sep">|</span>
      <span>&#9906; My Recent Searches</span>
    </div>
  </header>

  <section class="abs hero">
    <div class="section-label" style="top:44px">What it's About</div>
    <div class="video" style="top:88px">
      <div class="screen" role="img" aria-label="Video still: hand holding a smartphone" style="background:linear-gradient(135deg,#2c3a44,#6d7880 55%,#3a4650)">
        <div class="play"><svg width="26" height="30"><polygon points="3,0 26,15 3,30" fill="#111"/></svg></div>
      </div>
      <div class="controls">
        <svg width="12" height="12"><polygon points="0,0 12,6 0,12" fill="#222"/></svg>
        <svg width="10" height="10"><rect width="10" height="10" fill="#222"/></svg>
        <div class="progress"></div>
        <svg width="18" height="12"><rect x="0" y="9" width="2" height="3" fill="#222"/><rect x="5" y="6" width="2" height="6" fill="#222"/><rect x="10" y="3" width="2" height="9" fill="#222"/><rect x="15" y="0" width="2" height="12" fill="#222"/></svg>
      </div>
    </div>
    <div class="section-label" style="top:339px">What Velma does for charity</div>
    <div class="video" style="top:383px">
      <div class="screen" role="img" aria-label="Video still: hands using a phone shopping app" style="background:linear-gradient(135deg,#4a3a2e,#a08670 55%,#3b2f28)">
        <div class="play"><svg width="26" height="30"><polygon points="3,0 26,15 3,30" fill="#111"/></svg></div>
      </div>
      <div class="controls">
        <svg width="12" height="12"><polygon points="0,0 12,6 0,12" fill="#222"/></svg>
        <svg width="10" height="10"><rect width="10" height="10" fill="#222"/></svg>
        <div class="progress"></div>
        <svg width="18" height="12"><rect x="0" y="9" width="2" height="3" fill="#222"/><rect x="5" y="6" width="2" height="6" fill="#222"/><rect x="10" y="3" width="2" height="9" fill="#222"/><rect x="15" y="0" width="2" height="12" fill="#222"/></svg>
      </div>
    </div>

    <div class="promo" style="top:50px">
      <div class="thumb" role="img" aria-label="Smartphone product photo"><i></i></div>
      <h3>Nemo enim ipsam</h3><p>Nemo enim ipsam volup tatem quia voluptas sit.</p><a>Read More &gt;&gt;</a>
    </div>
    <div class="rule" style="top:209px"></div>
    <div class="promo" style="top:246px">
      <div class="thumb" role="img" aria-label="Smartphone product photo"><i></i></div>
      <h3>Nemo enim ipsam</h3><p>Nemo enim ipsam volup tatem quia voluptas sit.</p><a>Read More &gt;&gt;</a>
    </div>
    <div class="rule" style="top:405px"></div>
    <div class="promo" style="top:442px">
      <div class="thumb" role="img" aria-label="Tablet and phone product photo"><i style="width:86px;height:60px"></i></div>
      <h3>Nemo enim ipsam</h3><p>Nemo enim ipsam volup tatem quia voluptas sit.</p><a>Read More &gt;&gt;</a>
    </div>
    <div class="rule" style="top:600px"></div>
  </section>

  <form class="abs finder">
    <div class="photo" role="img" aria-label="Rose gold wristwatch with blue dial"></div>
    <div class="field" style="left:15px;top:216px;width:404px">Item<span class="q">?</span></div>
    <div class="field" style="left:15px;top:282px;width:404px">Location<span class="q">?</span></div>
    <div class="lbl" style="top:361px">From</div>
    <div class="field" style="left:82px;top:347px;width:337px">$<span class="q">?</span></div>
    <div class="lbl" style="top:427px">To</div>
    <div class="field" style="left:82px;top:414px;width:337px">$<span class="q">?</span></div>
    <div class="btn-search">SEARCH</div>
  </form>

  <section class="abs banner" role="img" aria-label="Close-up of a chronograph watch dial">
    <svg width="1140" height="265"><polygon points="892,0 1140,0 1140,265 768,265" fill="#d97a18"/></svg>
    <div class="mark">velma</div>
    <div class="tag">GET EXCLUSIVE ITEMS</div>
  </section>

  <section class="abs feedback">
    <h2 class="title-round">user feedback</h2>
    <div class="underline"></div>

    <div class="quote" style="left:25px">
      <svg width="369" height="240"><g transform="translate(0,23)"><path d="M1 1H368V194H32L2 212z" fill="none" stroke="#f78f20" stroke-width="2"/><circle cx="184" cy="1" r="22" fill="#f78f20"/><path d="M174 -5h20v12h-12l-6 5v-5h-2z" fill="none" stroke="#fff" stroke-width="2"/></g></svg>
      <p>“Nemo enim ipsam voluptatem quia voluptas sit aspernatur aut odit aut fugit, sed quia con sequuntur magni dolores eos qui ratione vo luptatem sequi nesciunt.”</p>
      <div class="name">- Halloway</div>
    </div>
    <div class="quote featured" style="left:416px">
      <svg width="369" height="240"><g transform="translate(0,23)"><path d="M1 1H368V194H32L2 212z" fill="#f78f20" stroke="#f78f20" stroke-width="2"/><circle cx="184" cy="1" r="22" fill="#fff" stroke="#f78f20" stroke-width="2"/><path d="M174 -5h20v12h-12l-6 5v-5h-2z" fill="none" stroke="#f78f20" stroke-width="2"/></g></svg>
      <p>“Nemo enim ipsam voluptatem quia voluptas sit aspernatur aut odit aut fugit, sed quia con sequuntur magni dolores eos qui ratione vo luptatem sequi nesciunt.”</p>
      <div class="name">- Peter Lane</div>
    </div>
    <div class="quote" style="left:806px">
      <svg width="369" height="240"><g transform="translate(0,23)"><path d="M1 1H368V194H32L2 212z" fill="none" stroke="#f78f20" stroke-width="2"/><circle cx="184" cy="1" r="22" fill="#f78f20"/><path d="M174 -5h20v12h-12l-6 5v-5h-2z" fill="none" stroke="#fff" stroke-width="2"/></g></svg>
      <p>“Nemo enim ipsam voluptatem quia voluptas sit aspernatur aut odit aut fugit, sed quia con sequuntur magni dolores eos qui ratione vo luptatem sequi nesciunt.”</p>
      <div class="name">- Ferris</div>
    </div>

    <div class="cta">Leave feedback for a chance to win a prize</div>
  </section>

  <section class="abs charities">
    <h2 class="title-round">charities supported</h2>
    <div class="underline"></div>

    <div class="badge" style="left:30px;top:143px"><i></i></div>
    <div class="badge" style="left:228px;top:143px"><i></i></div>
    <div class="badge" style="left:427px;top:143px"><i class="round" style="width:60px"></i></div>
    <div class="badge" style="left:30px;top:270px"><i></i></div>
    <div class="badge" style="left:228px;top:270px"><i class="round"></i></div>
    <div class="badge" style="left:427px;top:270px"><i></i></div>
    <div class="badge" style="left:30px;top:397px"><i></i></div>
    <div class="badge" style="left:228px;top:397px"><i class="round"></i></div>
    <div class="badge" style="left:427px;top:397px"><i></i></div>

    <div class="feature" style="top:57px;background:linear-gradient(120deg,#1e2a3a,#34465c 50%,#10161f)" role="img" aria-label="Man in a suit wearing a steel wristwatch">
      <span style="right:16px;top:142px">watch collections</span>
    </div>
    <div class="feature" style="top:280px;background:radial-gradient(ellipse at 55% 45%,#5a5a5a,#1a1a1a 60%,#050505)" role="img" aria-label="Black leather wristwatch on a dark wet surface">
      <span style="left:24px;top:138px">new trends</span>
    </div>
  </section>

  <footer class="abs footer">
    <div class="nav">About Velma<span class="sep">|</span>Safety Hub<span class="sep">|</span>Resolution Hub<span class="sep">|</span>Vendor Hub<span class="sep">|</span>Partner Hub<span class="sep">|</span>Charity Hub</div>
    <div class="social"><i></i><i></i><i></i><i></i><i></i><i></i><i></i></div>
    <hr>
    <div class="copy">Copyrights @ 2017 Velma. All rights reserved.</div>
    <div class="meta">Advertise on velma<span class="sep">|</span>Site Map</div>
  </footer>

</div>
</body>
</html>
```